Business Card for Industrial Distributor

We need a business card design for an industrial distributor. We sell machine parts for the manufacturing and oil industry. We would like the cards to look clean and modern but with a touch of industry.

Our colors are blue/white.

Please feel free to visit our website www.korvelpartsco.com

Target Market(s)

mexican manufacturers in the automobile/aerospace industry

Industry/Entity Type

Industrial

Colors
ffffff
0555a3

```html
<!DOCTYPE html>
<html lang="en">
<head>
<meta charset="utf-8">
<title>Korvel Business Card</title>
<link rel="stylesheet" href="https://fonts.googleapis.com/css2?family=Montserrat:wght@400;500;600;800&display=swap">
<style>
  :root {
    --stage: #e9ebee;
    --card: #0a5c8f;
    --white: #ffffff;
    --accent: #2e3192;
    --divider: rgba(46, 49, 146, 0.55);
  }
  * { margin: 0; padding: 0; box-sizing: border-box; }
  html, body {
    width: 1200px; height: 900px; overflow: hidden;
    background: var(--stage);
    font-family: "Montserrat", sans-serif;
  }
  .canvas { position: relative; width: 1200px; height: 900px; }
  .card {
    position: absolute; width: 600px; height: 343px;
    background: var(--card); border-radius: 20px; overflow: hidden;
    box-shadow: 0 10px 30px rgba(0,0,0,0.18);
  }
  /* Front */
  .card-front { left: 80px; top: 80px; }
  .front-brand {
    position: absolute; left: 0; right: 0; top: 96px;
    display: flex; align-items: center; justify-content: center; gap: 16px;
  }
  .front-brand .dot { width: 44px; height: 44px; border-radius: 50%; background: var(--white); }
  .front-brand .name {
    color: var(--white); font-weight: 800; font-size: 56px; letter-spacing: 1px;
  }
  .front-url {
    position: absolute; left: 0; right: 0; bottom: 52px; text-align: center;
    color: var(--white); font-size: 17px; font-weight: 400; letter-spacing: 0.5px;
  }
  .front-url strong { font-weight: 600; }
  /* Back */
  .card-back { left: 520px; top: 477px; }
  .edge-tab {
    position: absolute; right: 0; top: 0; width: 26px; height: 180px;
    background: var(--accent); border-bottom-left-radius: 26px;
  }
  .back-brand {
    position: absolute; left: 36px; bottom: 60px;
    display: flex; align-items: center; gap: 10px;
  }
  .back-brand .dot { width: 36px; height: 36px; border-radius: 50%; background: var(--accent); }
  .back-brand .name { color: var(--accent); font-weight: 800; font-size: 44px; }
  .divider {
    position: absolute; left: 318px; top: 70px; width: 1px; height: 170px;
    background: var(--divider);
  }
  .contact { position: absolute; left: 336px; top: 74px; color: var(--white); }
  .contact .person { color: var(--accent); font-weight: 600; font-size: 21px; line-height: 1.1; }
  .contact .role { font-size: 13px; margin: 3px 0 8px; }
  .contact .address { font-size: 13px; line-height: 1.45; margin-bottom: 8px; }
  .contact ul { list-style: none; }
  .contact li { display: flex; align-items: center; gap: 8px; font-size: 13px; line-height: 1.6; }
  .contact li svg { width: 11px; height: 11px; flex: none; }
  .contact .hl { color: var(--accent); }
</style>
</head>
<body>
<div class="canvas">

  <section class="card card-front">
    <div class="front-brand">
      <span class="dot"></span>
      <span class="name">Korvel</span>
    </div>
    <p class="front-url">www.<strong>korvelparts</strong>co.com</p>
  </section>

  <section class="card card-back">
    <div class="edge-tab"></div>
    <div class="back-brand">
      <span class="dot"></span>
      <span class="name">Korvel</span>
    </div>
    <div class="divider"></div>
    <div class="contact">
      <p class="person">Marcus Delaney</p>
      <p class="role">Director</p>
      <p class="address">P.O. Box 4817<br>Lansing, MI 48901</p>
      <ul>
        <li>
          <svg viewBox="0 0 12 12"><path d="M3 1l2 2.5-1.2 1.3a7 7 0 0 0 3.4 3.4L8.5 7 11 9l-1.3 1.8C5.5 10.5 1.5 6.5 1.2 2.3z" fill="#2e3192"/></svg>
          +330 5183-2947
        </li>
        <li>
          <svg viewBox="0 0 12 12"><rect x="1" y="2.5" width="10" height="7" rx="1" fill="#2e3192"/><path d="M1.5 3l4.5 3.5L10.5 3" stroke="#0a5c8f" fill="none"/></svg>
          info@korvelpartsco.com
        </li>
        <li>
          <svg viewBox="0 0 12 12"><circle cx="6" cy="6" r="5" fill="#2e3192"/></svg>
          <span>www.<span class="hl">korvelparts</span>co.com</span>
        </li>
      </ul>
    </div>
  </section>

</div>
</body>
</html>
```